Site for entrepreneurs/small businesses needs Logo, Homepage

Looking for a logo, either an icon, or stylized text, or a combination of both, and a home page design which fits with it. The logo will be for use on the public website as well as for printed collateral (business cards, post cards, brochures and various other marketing materials).

The site is called Orbitwell (Orbitwell.example). This is to be a national, and eventually an international brand. The new service will provide an easy-to-use platform for entrepreneurs to build their business and web presence together in an integrated way which allows them to focus on their core competency.

The site/service will be dead-simple to use, A/B/C, 1/2/3. We will want some sort of "Get started for FREE" promotional space to collect the person's email address with multiple points of interest which guide the user back to this one call to action: sign up for free. We will feature editorial/blog stories, customer testimonials, and present several key features the the reader just can't live without if they are starting a new business.

Criteria:
* Refer to our comparable sites/logos in the design document attached
* Incorporate our color scheme (but complementary colors welcome)
* No Serif fonts!
* No photo-realistic elements for logo
* Logo must present well in gray scale and/or black/white (for printed materials)
* Strokes/borders that are wider to promote simplicity (vs. thin/precise lines which promote technical complexity)

Inspirations:
* Creative/Custom (but legible) fonts
* Excitement, energetic, jumping for joy
* Karate / Ninja / Power / Precision
* Dance Moves
* Regional influences: California, Silicon Valley, West Coast, Surf City, Beaches, Sunset
* Simple/easy, no-brainer solutions

Target Market(s)

Small Businesses / Entrepreneurs

Logo Text

Orbitwell or Orbitwell.example

Number of Pages Required

1 page

Font styles to use
Sans Serif
Decorative

Requirements
Must have
• See the attached style guide (PDF)

```html
<!DOCTYPE html>
<html lang="en">
<head>
<meta charset="utf-8">
<title>Orbitwell — Build your business</title>
<link rel="stylesheet" href="https://fonts.googleapis.com/css2?family=Montserrat:wght@400;600;700;800&family=Open+Sans:wght@400;600&display=swap">
<style>
:root{
  --hero:#12303d;
  --navy:#0f2344;
  --ink:#1a2b4c;
  --orange:#f7931e;
  --cyan:#1fe8f0;
  --grey-band:#f3f4f6;
  --text:#3a3f4a;
  --muted:#8a93a3;
  --social:#2b8bd6;
  --white:#ffffff;
}
*{margin:0;padding:0;box-sizing:border-box}
html,body{width:1200px;height:4433px;overflow:hidden}
body{position:relative;background:var(--white);font-family:"Open Sans",sans-serif;color:var(--text)}
.abs{position:absolute}
.band{position:absolute;left:0;width:1200px}
.band svg{display:block}
h1,h2,h3,.nav,.btn{font-family:"Montserrat",sans-serif}
.btn{position:absolute;display:flex;align-items:center;justify-content:center;background:var(--orange);color:var(--white);font-weight:700;text-transform:uppercase;border-radius:30px;letter-spacing:.3px}
.brand{display:flex;align-items:center;gap:12px;font-family:"Montserrat",sans-serif;font-weight:700;color:var(--white)}
.brand .dot{width:34px;height:34px;border-radius:50%;background:var(--orange)}
.art{position:absolute;border-radius:6px}

/* hero */
.nav{position:absolute;top:27px;left:676px;display:flex;gap:30px;font-size:13px;font-weight:700;color:var(--white)}
.nav .active{color:var(--orange)}
.hero-title{position:absolute;left:136px;top:196px;font-size:37px;line-height:42px;font-weight:800;color:var(--white)}
.field{position:absolute;left:136px;width:275px;height:40px;background:#eceef0;border-radius:6px;display:flex;align-items:center;padding-left:18px;gap:12px;font-size:13px;color:#333}
.field i{width:10px;height:10px;border-radius:50%;background:#555;display:block}

/* welcome */
.welcome-mark{position:absolute;left:736px;top:836px;width:54px;height:54px;border-radius:50%;background:var(--orange)}
.welcome-kicker{position:absolute;left:828px;top:834px;font-family:"Montserrat",sans-serif;font-weight:800;font-size:17px;color:var(--ink)}
.welcome-name{position:absolute;left:826px;top:854px;font-family:"Montserrat",sans-serif;font-weight:700;font-size:48px;color:var(--ink)}
.copy{font-size:13.5px;line-height:20px;color:var(--text)}

/* titles */
.section-title{position:absolute;left:0;width:1200px;text-align:center;font-size:26px;font-weight:800;color:var(--ink)}
.rule{position:absolute;left:570px;width:60px;height:5px;background:#cfd3d9;border-radius:3px}

/* services */
.card{position:absolute;width:222px;height:288px;background:var(--white);box-shadow:0 4px 16px rgba(0,0,0,.12);border-radius:4px;text-align:center}
.card .icon{width:56px;height:56px;margin:36px auto 0;border-radius:12px;background:var(--ink)}
.card h3{margin-top:22px;font-size:15px;font-weight:700;color:#111}
.card p{margin:20px 24px 0;font-size:12px;line-height:17px;color:var(--text)}
.card .btn{position:static;margin:22px auto 0;width:88px;height:26px;font-size:10px}

/* features */
.feat-list{position:absolute;left:146px;top:2500px;list-style:none;font-size:12.5px;line-height:20.5px;color:var(--text)}
.feat-list li{position:relative;padding-left:22px}
.feat-list li::before{content:"";position:absolute;left:0;top:8px;width:6px;height:6px;border-radius:50%;background:var(--orange)}

/* blog */
.post{position:absolute;top:3086px;width:278px;height:388px;background:var(--white);box-shadow:0 4px 16px rgba(0,0,0,.12)}
.post .thumb{height:218px}
.post h3{margin:14px 38px 0 38px;font-size:14px;line-height:18px;font-weight:800;color:#111}
.post p{margin:14px 38px 0;font-size:12px;line-height:16px}
.post .btn{position:static;margin:14px 0 0 38px;width:88px;height:26px;font-size:10px}

/* testimonials */
.quote-card{position:absolute;left:520px;top:3683px;width:540px;height:220px;background:var(--white);border-radius:60px 10px 60px 10px;z-index:2}
.stars{position:absolute;left:86px;top:30px;color:var(--navy);font-size:14px;letter-spacing:2px}
.qmark{position:absolute;font-family:"Montserrat",sans-serif;font-size:44px;color:#c4c9d2;font-weight:700}

/* footer */
.foot-h{position:absolute;top:4110px;font-family:"Montserrat",sans-serif;font-weight:700;font-size:13px;color:var(--white)}
.foot-list{position:absolute;list-style:none;font-size:12px;color:#d4dae6;line-height:18px}
.foot-row{display:flex;align-items:center;gap:14px;margin-bottom:14px}
.foot-row b{display:block;width:14px;height:14px;border-radius:50%;background:var(--white);flex:none}
.social b{width:22px;height:22px;background:var(--social)}
</style>
</head>
<body>

<!-- HERO -->
<div class="band" style="top:0">
  <svg width="1200" height="710" viewBox="0 0 1200 710"><polygon points="0,0 1200,0 1200,560 0,708" fill="var(--hero)"/></svg>
</div>
<div class="brand abs" style="left:133px;top:32px;font-size:36px"><span class="dot"></span>Orbitwell</div>
<nav class="nav"><span class="active">HOME</span><span>ABOUT US</span><span>SERVICES</span><span>BLOG</span><span>CONTACT US</span></nav>
<h1 class="hero-title">GET STARTED<br>FOR FREE</h1>
<div class="field" style="top:312px"><i></i>E mail id</div>
<div class="field" style="top:366px"><i></i>Name</div>
<div class="btn" style="left:136px;top:437px;width:276px;height:46px;font-size:15px">Sign up for free</div>
<div class="art" role="img" aria-label="Illustration of a person working at a desk with floating charts and dashboards" style="left:562px;top:150px;width:530px;height:486px;background:linear-gradient(160deg,#e9eef5 0%,#b9c6db 55%,#c24a3c 100%);opacity:.9"></div>

<!-- WELCOME -->
<div class="art" role="img" aria-label="Isometric illustration of a business city with people, screens and charts" style="left:60px;top:754px;width:620px;height:458px;background:linear-gradient(150deg,#eef0fb 0%,#b8bdf0 55%,#f3d452 100%)"></div>
<div class="welcome-mark"></div>
<div class="welcome-kicker">WELCOME TO</div>
<div class="welcome-name">Orbitwell</div>
<p class="copy abs" style="left:736px;top:952px;width:420px">At vero eos et accusamus et iusto odio dignissimos ducimus qui blanditiis praesentium voluptatum deleniti atque corrupti quos dolores et quas molestias excepturi sint occaecati cupiditate non provident, similique sunt in culpa qui officia deserunt mollitia.</p>
<div class="btn" style="left:736px;top:1094px;width:134px;height:40px;font-size:12px">Read more</div>

<!-- SERVICES -->
<div class="band" style="top:1240px">
  <svg width="1200" height="1060" viewBox="0 0 1200 1060"><polygon points="0,100 1200,0 1200,960 0,1050" fill="var(--grey-band)"/></svg>
</div>
<h2 class="section-title" style="top:1384px">OUR SERVICES</h2>
<div class="rule" style="top:1436px"></div>

<div class="card" style="left:133px;top:1525px"><div class="icon" role="img" aria-label="Entrepreneur icon"></div><h3>Entrepreneurs</h3><p>At vero eos et accusamus et iusto odio dignissimos ducimus qui blan ditiis praesentium.</p><div class="btn">Read more</div></div>
<div class="card" style="left:372px;top:1525px"><div class="icon" role="img" aria-label="Handshake icon"></div><h3>Build Business</h3><p>At vero eos et accusamus et iusto odio dignissimos ducimus qui blan ditiis praesentium.</p><div class="btn">Read more</div></div>
<div class="card" style="left:609px;top:1525px"><div class="icon" role="img" aria-label="Puzzle icon"></div><h3>Easy to Use</h3><p>At vero eos et accusamus et iusto odio dignissimos ducimus qui blan ditiis praesentium.</p><div class="btn">Read more</div></div>
<div class="card" style="left:847px;top:1525px"><div class="icon" role="img" aria-label="Headset icon"></div><h3>Support</h3><p>At vero eos et accusamus et iusto odio dignissimos ducimus qui blan ditiis praesentium.</p><div class="btn">Read more</div></div>
<div class="card" style="left:133px;top:1838px"><div class="icon" role="img" aria-label="Chat bubbles icon"></div><h3>Customer Satisfaction</h3><p>At vero eos et accusamus et iusto odio dignissimos ducimus qui blan ditiis praesentium.</p><div class="btn">Read more</div></div>
<div class="card" style="left:372px;top:1838px"><div class="icon" role="img" aria-label="Training board icon"></div><h3>Training</h3><p>At vero eos et accusamus et iusto odio dignissimos ducimus qui blan ditiis praesentium.</p><div class="btn">Read more</div></div>
<div class="card" style="left:609px;top:1838px"><div class="icon" role="img" aria-label="Help business icon"></div><h3>Help Business</h3><p>At vero eos et accusamus et iusto odio dignissimos ducimus qui blan ditiis praesentium.</p><div class="btn">Read more</div></div>
<div class="card" style="left:847px;top:1838px"><div class="icon" role="img" aria-label="Growth chart icon"></div><h3>Successful Business</h3><p>At vero eos et accusamus et iusto odio dignissimos ducimus qui blan ditiis praesentium.</p><div class="btn">Read more</div></div>

<!-- FEATURES -->
<h2 class="abs" style="left:146px;top:2362px;font-size:27px;font-weight:800;color:var(--ink)">FEATURES</h2>
<p class="copy abs" style="left:146px;top:2424px;width:380px;font-size:14px">At vero eos et accusamus et iusto odio dignissimos ducimus qui blanditiis praesentium voluptatum.</p>
<ul class="feat-list">
  <li>Lorem Ipsum is simply dummy text of the printing</li>
  <li>Contrary to popular belief</li>
  <li>It is a long established fact that a</li>
  <li>There are many variations of passages of Lorem</li>
  <li>Contrary to popular belief lorem</li>
  <li>Sed ut perspiciatis unde omnis</li>
</ul>
<div class="btn" style="left:146px;top:2689px;width:134px;height:40px;font-size:12px">Read more</div>
<div class="art" role="img" aria-label="Isometric illustration of a team collaborating around screens and documents" style="left:532px;top:2362px;width:606px;height:476px;border-radius:50%;background:radial-gradient(ellipse at center,#a9d8f2 0%,#dcefff 60%,#ffffff 100%)"></div>

<!-- BLOG -->
<div class="band" style="top:2880px;height:660px;background:#fafafa"></div>
<h2 class="section-title" style="top:2945px">LATEST BLOG</h2>
<div class="rule" style="top:2996px"></div>
<div class="post" style="left:148px"><div class="thumb" role="img" aria-label="Blog image: business icons around a laptop" style="background:linear-gradient(135deg,#1f7f93,#2aa3b6)"></div><h3>LOREM IPSUM DOLOR SIT SECTETUR ADIPISCI</h3><p>Lorem ipsum dolor sit amet, consectetur adipiscing elit, sed do eiusmod tempor</p><div class="btn">Read more</div></div>
<div class="post" style="left:458px"><div class="thumb" role="img" aria-label="Blog image: businessman on a stack of books" style="background:linear-gradient(135deg,#1b8aa6,#34b4cf)"></div><h3>LOREM IPSUM DOLOR SIT SECTETUR ADIPISCI</h3><p>Lorem ipsum dolor sit amet, consectetur adipiscing elit, sed do eiusmod tempor</p><div class="btn">Read more</div></div>
<div class="post" style="left:758px"><div class="thumb" role="img" aria-label="Blog image: team climbing a mountain to a flag" style="background:linear-gradient(180deg,#3aa8f0,#bfe4fb)"></div><h3>LOREM IPSUM DOLOR SIT SECTETUR ADIPISCI</h3><p>Lorem ipsum dolor sit amet, consectetur adipiscing elit, sed do eiusmod tempor</p><div class="btn">Read more</div></div>

<!-- TESTIMONIALS -->
<div class="band" style="top:3530px">
  <svg width="1200" height="540" viewBox="0 0 1200 540"><polygon points="0,90 1200,0 1200,520 0,540" fill="var(--cyan)"/></svg>
</div>
<div class="abs" style="left:146px;top:3686px;font-family:Montserrat,sans-serif;font-weight:700;font-size:18px;color:var(--navy)">TESTIMONIALS</div>
<h2 class="abs" style="left:146px;top:3714px;font-size:36px;font-weight:800;color:#1d4fb0">HAPPY CLIENTS</h2>
<div class="art" role="img" aria-label="Illustration of a megaphone with gears and a light bulb" style="left:330px;top:3900px;width:180px;height:130px;background:linear-gradient(135deg,#ffffff 0%,#b8e9f2 50%,#f15a4a 100%);border-radius:40%"></div>
<div class="quote-card">
  <div class="qmark" style="left:50px;top:18px">&ldquo;</div>
  <div class="stars">★★★★★</div>
  <p class="copy abs" style="left:86px;top:58px;width:400px;font-size:12.5px;line-height:17px">At vero eos et accusamus et iusto odio dignissimos ducimus qui blanditiis praesentium voluptatum deleniti atque corrupti quos dolores et quas molestias excepturi sint occaecati cupiditate non provident, similique sunt in culpa</p>
  <div class="qmark" style="left:420px;top:128px">&rdquo;</div>
  <div class="abs" style="left:86px;top:150px;width:50px;height:3px;background:var(--cyan)"></div>
  <div class="abs" style="left:86px;top:158px;font-size:10px;color:#1d4fb0">Client Name</div>
  <div class="abs" style="left:86px;top:172px;font-size:9px;color:var(--muted)">Founder</div>
</div>
<div class="abs" style="left:968px;top:3920px;display:flex;gap:9px">
  <span style="width:10px;height:10px;border-radius:50%;background:#fff"></span>
  <span style="width:10px;height:10px;border-radius:50%;background:#fff"></span>
  <span style="width:10px;height:10px;border-radius:50%;background:var(--navy)"></span>
  <span style="width:10px;height:10px;border-radius:50%;background:#fff"></span>
  <span style="width:10px;height:10px;border-radius:50%;background:#fff"></span>
</div>

<!-- FOOTER -->
<div class="band" style="top:4020px">
  <svg width="1200" height="413" viewBox="0 0 1200 413"><polygon points="0,40 1200,0 1200,413 0,413" fill="var(--navy)"/></svg>
</div>
<div class="brand abs" style="left:133px;top:4168px;font-size:38px"><span class="dot"></span>Orbitwell</div>

<div class="foot-h" style="left:479px">CONTACT US</div>
<div class="foot-list" style="left:479px;top:4144px">
  <div class="foot-row" style="align-items:flex-start"><b></b><span>118 Harbor Lane,<br>Bayview, CA 90000</span></div>
  <div class="foot-row"><b></b><span>555.010.0199</span></div>
  <div class="foot-row"><b></b><span>info@orbitwell.example</span></div>
</div>

<div class="foot-h" style="left:736px">MENU</div>
<ul class="foot-list" style="left:736px;top:4144px;line-height:16px">
  <li>Home</li><li>About Us</li><li>Services</li><li>Blog</li><li>Contact Us</li>
</ul>

<div class="foot-h" style="left:940px">CONNECT WITH US</div>
<div class="foot-list social" style="left:940px;top:4150px">
  <div class="foot-row"><b></b><span>Circlepost</span></div>
  <div class="foot-row"><b></b><span>Feedline</span></div>
  <div class="foot-row"><b></b><span>Worknet</span></div>
</div>

<div class="abs" style="left:0;top:4368px;width:1200px;text-align:center;font-size:11px;color:#c9d0dc">Copyrights @ 2018 All Rights Reserved</div>

</body>
</html>
```